Harwick Moss Fine Art gallery website - Modern british art for sale

We need a website design that is both current and high end. Our products are expensive and this should be reflected in the look of the website. We would like the logo we had designed last year to be clearly seen in the design. We want sleek, simple, and easy to navigate. Nothing too colourful as the colours of the art should always take precedence.

Target Market(s)

The average price of one our products starts at £250 and can go up to £10,000 we are an entry level gallery.

Industry/Entity Type

Art Gallery

Number of Pages Required

5+ page

Font styles to use
Sans Serif

Colors
000000
ffffff
faa54b
abd037
886aae
b868aa

Requirements
Must have
• Attractive front page. Linked to our Chirp feed.
• 4 links from front page - New Releases, about us, Artists, contact us
• Social media links - Facebook, Chirp, YouTube, Instagram.
• Each artist must have their own page, each page must have a biography link to another page.
Nice to have
• Utilise our new logo design. I would like the Chirp feed to link to the front page in a small way so you can see what's being said on Chirp by the company. For future proofing maybe have a locations function on the front page which can be adroit down menu showing where our other galleries are.

```html
<!DOCTYPE html>
<html lang="en">
<head>
<meta charset="utf-8">
<title>Harwick Moss Fine Art – Modern British Art</title>
<link rel="stylesheet" href="https://fonts.googleapis.com/css2?family=Lato:wght@400;700&family=Lora:wght@400;500&display=swap">
<style>
:root{
  --black:#000000;
  --white:#ffffff;
  --ink:#222222;
  --muted:#666666;
  --line:#dddddd;
  --card:#f1f1f1;
  --plum:#b868aa;
  --violet:#886aae;
  --teal:#6fb7c9;
  --feed-bg:#cfe9ea;
  --feed-blue:#3aa1e0;
  --orange:#faa54b;
  --green:#abd037;
}
*{box-sizing:border-box;margin:0;padding:0}
html,body{width:1200px;height:3056px;overflow:hidden;background:var(--white)}
body{font-family:'Lato',Arial,sans-serif;color:var(--ink);position:relative}
.wrap{position:absolute;left:86px;width:1028px}
a{color:inherit;text-decoration:none}

/* header */
.brand{position:absolute;left:86px;top:30px;display:flex;align-items:center;gap:14px}
.brand-dot{width:34px;height:34px;border-radius:50%;background:var(--teal)}
.brand-name{font-family:'Lora',Georgia,serif;font-size:31px;color:var(--black);letter-spacing:.5px}
.account{position:absolute;right:86px;top:32px;display:flex;gap:14px;align-items:center;font-size:13px}
.account .sq{width:13px;height:13px;background:var(--ink)}
.account .sep{width:1px;height:14px;background:var(--ink)}
.mainnav{position:absolute;right:86px;top:58px;display:flex;gap:22px;align-items:center;font-size:13px;letter-spacing:.3px}
.mainnav .active{border:1px solid #999;border-radius:3px;padding:5px 8px}

/* hero */
.hero{top:112px;height:428px;overflow:hidden}
.hero-bg{position:absolute;inset:0;background:
  radial-gradient(circle at 20% 80%,#a56fbf 0,transparent 45%),
  radial-gradient(circle at 75% 20%,#9ccf5a 0,transparent 40%),
  radial-gradient(circle at 55% 60%,#c49a6a 0,transparent 35%),
  linear-gradient(120deg,#7fc7d8,#bfe3e6 50%,#8fc9d4)}
.hero-copy{position:absolute;left:57px;top:108px;color:var(--white);width:480px}
.hero-copy h1{font-family:'Lora',Georgia,serif;font-weight:400;font-size:50px;letter-spacing:1px;margin-bottom:14px}
.hero-copy p{font-size:13px;line-height:24px}
.btn-plum{display:inline-block;background:var(--plum);color:var(--white);font-size:17px;padding:13px 24px;margin-top:28px;border-radius:2px}
.frame{position:absolute;left:617px;top:71px;width:316px;height:281px;background:#c98a3c;border:3px solid #a8692a;padding:14px;box-shadow:20px 22px 30px rgba(0,0,0,.2)}
.frame-mat{width:100%;height:100%;background:var(--white);padding:26px}
.frame-art{width:100%;height:100%;background:linear-gradient(135deg,#e9eef0,#d7dde0 60%,#c9d3d6)}

/* section headings */
.heading{text-align:center;font-family:'Lora',Georgia,serif;font-weight:400;font-size:30px;color:var(--black)}
.heading::after{content:"";display:block;width:136px;height:3px;background:var(--black);margin:14px auto 0}

/* arrows */
.arrow{position:absolute;width:24px;height:24px}

/* products */
.products{top:693px;display:flex;gap:14px}
.product{width:247px;text-align:center}
.product-art{height:299px;border:1px solid var(--line);padding:12px;background:var(--white)}
.product.lift .product-art{box-shadow:0 4px 16px rgba(0,0,0,.25)}
.product-art div{width:100%;height:100%}
.product h3{font-weight:400;font-size:15px;letter-spacing:.4px;margin-top:27px;color:var(--black)}
.buy{display:flex;justify-content:center;align-items:center;gap:10px;margin-top:14px;font-size:15px}
.cart{background:var(--black);color:var(--white);font-size:13px;padding:4px 10px}
.lift .cart{background:var(--plum)}

/* artists */
.artists{top:1259px;display:flex;gap:15px}
.artist{width:193px}
.portrait{height:177px;border:1px solid var(--line)}
.artist.lift .portrait{box-shadow:0 3px 12px rgba(0,0,0,.25)}
.artist h4{font-weight:400;font-size:15px;margin-top:14px;color:var(--black)}
.artist span{font-size:12px;display:block;margin-top:6px}
.artist.lift h4,.artist.lift span{color:var(--plum)}

/* news */
.news{top:1676px;display:flex;gap:25px}
.story{width:326px;height:518px;background:var(--card);border:1px solid var(--line);padding:14px}
.story.lift{box-shadow:0 4px 16px rgba(0,0,0,.3)}
.story-img{height:279px}
.story h5{font-size:14px;font-weight:700;line-height:19px;margin-top:18px;color:var(--black)}
.story.lift h5{color:var(--plum);font-weight:400}
.story time{display:block;color:var(--teal);font-size:13px;margin-top:10px}
.story p{font-size:11px;line-height:18px;color:var(--muted);margin-top:10px}
.more{display:inline-block;font-size:11px;margin-top:18px;padding-bottom:4px;border-bottom:1px solid var(--ink)}
.story.lift .more{color:var(--plum);border-color:var(--plum)}

/* about */
.about{position:absolute;left:86px;top:2298px;width:560px}
.about h2{font-family:'Lora',Georgia,serif;font-weight:400;font-size:26px;color:var(--black);margin-bottom:28px}
.about p{font-size:15px;line-height:25px;color:#333;margin-bottom:25px}
.btn-black{display:inline-block;background:var(--black);color:var(--white);font-size:15px;padding:15px 26px;margin-top:2px}
.feed{position:absolute;left:668px;top:2302px;width:446px;height:279px;background:var(--feed-bg);padding:18px 24px}
.feed h2{font-family:'Lora',Georgia,serif;font-weight:400;font-size:26px;color:var(--black);padding-bottom:10px;border-bottom:1px solid #9fc}
.feed-badge{position:absolute;right:-2px;top:-28px;width:78px;height:78px;border-radius:50%;background:var(--feed-blue)}
.post{background:var(--white);margin-top:26px;padding:12px 14px;font-family:Arial,sans-serif;font-size:12px;line-height:17px;color:#222;position:relative}
.post-head{display:flex;gap:10px;align-items:center;margin-bottom:10px}
.post-avatar{width:30px;height:30px;background:#222}
.post-head b{display:block;font-size:13px}
.post-head small{color:#888}
.follow{position:absolute;right:12px;top:12px;border:1px solid #ccc;border-radius:3px;padding:3px 10px;font-size:11px;color:#3a8fd1}
.post a{color:#3a8fd1}
.post-meta{color:#888;font-size:11px;margin-top:4px}
.post-actions{display:flex;gap:18px;margin-top:8px}
.post-actions i{width:10px;height:8px;background:#999;display:block}

/* footer */
.footer{position:absolute;left:0;top:2715px;width:1200px;height:341px;background:var(--black);color:var(--white);overflow:hidden}
.footer-wash{position:absolute;inset:0;background:
  radial-gradient(ellipse at 85% 75%,rgba(255,255,255,.35) 0,transparent 30%),
  radial-gradient(ellipse at 55% 90%,rgba(255,255,255,.25) 0,transparent 25%),
  radial-gradient(ellipse at 10% 10%,rgba(255,255,255,.12) 0,transparent 25%)}
.fcol{position:absolute;top:45px}
.fcol h6{font-size:15px;font-weight:400;padding-bottom:12px;border-bottom:1px solid #555;width:270px;margin-bottom:16px}
.contact{display:flex;gap:22px;font-size:12px;line-height:20px;margin-bottom:12px}
.contact svg{flex:none;margin-top:4px}
.socials{display:flex;gap:10px;margin-top:14px}
.socials i{width:18px;height:18px;background:var(--white);display:block}
.links{font-size:12px;line-height:22px;list-style:none}
.fcol p{font-size:12px;line-height:20px;width:270px}
.signup{display:flex;margin-top:22px;width:265px;height:40px}
.signup span{flex:1;background:var(--white);color:#777;font-size:12px;padding:13px 20px}
.signup b{width:56px;background:var(--plum);display:flex;align-items:center;justify-content:center}
.copyright{position:absolute;left:86px;top:302px;font-size:11px}
</style>
</head>
<body>

<header>
  <div class="brand"><span class="brand-dot"></span><span class="brand-name">Harwick Moss Fine Art</span></div>
  <div class="account">
    <span>LOGIN</span><span class="sep"></span><span>JOIN</span>
    <span class="sq"></span><span class="sq"></span><span class="sq"></span><span class="sq"></span>
  </div>
  <nav class="mainnav">
    <a class="active">HOME</a><a>NEW RELEASES</a><a>ABOUT US</a><a>ARTISTS</a><a>CONTACT US</a><a>CART</a>
    <svg width="14" height="14" viewBox="0 0 14 14"><circle cx="6" cy="6" r="4.5" fill="none" stroke="#222" stroke-width="2"/><line x1="9" y1="9" x2="13" y2="13" stroke="#222" stroke-width="2"/></svg>
  </nav>
</header>

<section class="wrap hero">
  <div class="hero-bg" role="img" aria-label="Soft watercolour wash in blue, green, violet and ochre"></div>
  <div class="hero-copy">
    <h1>FINE ART PRINTS</h1>
    <p>Lorem Ipsum is simply dummy text of the printing and typesetting industry.<br>Lorem Ipsum has been the industry's standard dummy text ever since the 1500s,<br>when an unknown printer took a</p>
    <a class="btn-plum">Shop Now &gt;</a>
  </div>
  <div class="frame"><div class="frame-mat"><div class="frame-art" role="img" aria-label="Framed abstract print with a red and blue line"></div></div></div>
</section>
<svg class="arrow" style="left:44px;top:305px" viewBox="0 0 24 24"><circle cx="12" cy="12" r="11" fill="#eee" stroke="#bbb"/><path d="M14 7l-5 5 5 5" fill="none" stroke="#777" stroke-width="2"/></svg>
<svg class="arrow" style="left:1132px;top:305px" viewBox="0 0 24 24"><circle cx="12" cy="12" r="11" fill="#eee" stroke="#bbb"/><path d="M10 7l5 5-5 5" fill="none" stroke="#777" stroke-width="2"/></svg>

<h2 class="heading wrap" style="top:600px">Our Products</h2>
<section class="wrap products">
  <div class="product"><div class="product-art"><div role="img" aria-label="Painting of a skier in blue and ochre" style="background:linear-gradient(160deg,#f4f4f2,#c9cfd8 55%,#d9b77a)"></div></div><h3>DUNCAN HARLOW REID</h3><div class="buy">£450.00 <span class="cart">ADD TO CART</span></div></div>
  <div class="product lift"><div class="product-art"><div role="img" aria-label="Ink drawing of dark figures" style="background:linear-gradient(160deg,#f6f6f4,#cfcfcc 60%,#9a9a98)"></div></div><h3>JAMES PELLOW</h3><div class="buy">£550.00 <span class="cart">ADD TO CART</span></div></div>
  <div class="product"><div class="product-art"><div role="img" aria-label="Black line drawing of swirling forms" style="background:linear-gradient(160deg,#f4f4f4,#bdbdbd 55%,#7d7d7d)"></div></div><h3>ELEANOR FENWICK</h3><div class="buy">£350.00 <span class="cart">ADD TO CART</span></div></div>
  <div class="product"><div class="product-art"><div role="img" aria-label="Drawing of a church tower with an orange building" style="background:linear-gradient(160deg,#f6f4f0,#b8b3ad 55%,#d8653a)"></div></div><h3>BEATRICE HOLLOWAY</h3><div class="buy">£850.00 <span class="cart">ADD TO CART</span></div></div>
</section>
<svg class="arrow" style="left:44px;top:826px" viewBox="0 0 24 24"><circle cx="12" cy="12" r="11" fill="#eee" stroke="#bbb"/><path d="M14 7l-5 5 5 5" fill="none" stroke="#777" stroke-width="2"/></svg>
<svg class="arrow" style="left:1122px;top:826px" viewBox="0 0 24 24"><circle cx="12" cy="12" r="11" fill="#eee" stroke="#bbb"/><path d="M10 7l5 5-5 5" fill="none" stroke="#777" stroke-width="2"/></svg>

<h2 class="heading wrap" style="top:1179px">Featured Artists</h2>
<section class="wrap artists">
  <div class="artist"><div class="portrait" role="img" aria-label="Portrait photograph of the artist" style="background:linear-gradient(160deg,#b7c6d6,#8fa4ba)"></div><h4>Felix Ashdown</h4><span>British</span></div>
  <div class="artist"><div class="portrait" role="img" aria-label="Portrait photograph of the artist" style="background:linear-gradient(160deg,#f2c9d3,#e4a9ba)"></div><h4>Jonah Bellamy</h4><span>British</span></div>
  <div class="artist lift"><div class="portrait" role="img" aria-label="Portrait photograph of the artist" style="background:linear-gradient(160deg,#f2f2f2,#c9d3e0)"></div><h4>Philip Brandt</h4><span>Paris</span></div>
  <div class="artist"><div class="portrait" role="img" aria-label="Portrait photograph of the artist" style="background:linear-gradient(160deg,#c9c0b6,#a69c92)"></div><h4>Owen Caldecott</h4><span>Terracotta Vase</span></div>
  <div class="artist"><div class="portrait" role="img" aria-label="Portrait photograph of the artist" style="background:linear-gradient(160deg,#eeeeee,#b9c7d8)"></div><h4>Felix Ashdown</h4><span>British</span></div>
</section>
<svg class="arrow" style="left:44px;top:1343px" viewBox="0 0 24 24"><circle cx="12" cy="12" r="11" fill="#eee" stroke="#bbb"/><path d="M14 7l-5 5 5 5" fill="none" stroke="#777" stroke-width="2"/></svg>
<svg class="arrow" style="left:1122px;top:1343px" viewBox="0 0 24 24"><circle cx="12" cy="12" r="11" fill="#eee" stroke="#bbb"/><path d="M10 7l5 5-5 5" fill="none" stroke="#777" stroke-width="2"/></svg>

<h2 class="heading wrap" style="top:1596px">Our Latest News</h2>
<section class="wrap news">
  <article class="story"><div class="story-img" role="img" aria-label="Gallery installation with a red and blue line" style="background:linear-gradient(160deg,#eef0f2,#cdd3d8)"></div><h5>Northgate Academy to show Valdoria's exceptional National treasures.</h5><time>Feb 10, 2017.</time><p>The Northgate Academy in London is showing a phenomenal array of art from one of Europes finest State collections. The collection which will go on display in September include works by Corvel, Estrano, Gavard,</p><a class="more">read more &nbsp;»</a></article>
  <article class="story lift"><div class="story-img" role="img" aria-label="Photograph of a dark farmhouse on a moor" style="background:linear-gradient(180deg,#e6e9ea 0,#cfd3d4 55%,#3b3d36 70%,#5a5f4b)"></div><h5>Northgate Academy to show Valdoria's exceptional National treasures.</h5><time>Feb 10, 2017.</time><p>The Northgate Academy in London is showing a phenomenal array of art from one of Europes finest State collections. The collection which will go on display in September include works by Corvel, Estrano, Gavard,</p><a class="more">read more &nbsp;»</a></article>
  <article class="story"><div class="story-img" role="img" aria-label="Abstract painting in sepia and white" style="background:linear-gradient(150deg,#c58a4f,#e8d3b8 45%,#f7f2ea 60%,#b9834a)"></div><h5>Northgate Academy to show Valdoria's exceptional National treasures.</h5><time>Feb 10, 2017.</time><p>The Northgate Academy in London is showing a phenomenal array of art from one of Europes finest State collections. The collection which will go on display in September include works by Corvel, Estrano, Gavard,</p><a class="more">read more &nbsp;»</a></article>
</section>

<section class="about">
  <h2>About Harwick Moss Fine Art</h2>
  <p>Set up in the year 2000 by Brothers Graham and Michael Thorne, Harwick Moss Fine Art quickly came to the fore front of Modern British Art. With varied collections mainly leaning to the Northern School of Art at first, then branching out into some of the leading names in the British Art world.</p>
  <p>The first home of Harwick Moss Fine Art was at the famous Harbour Quay complex in Liverpool City Centre. The Gallery then became an online Gallery with offices in London where consultations could take place with clients.</p>
  <a class="btn-black">Read More &gt;</a>
</section>

<aside class="feed">
  <span class="feed-badge"></span>
  <h2>Chirp</h2>
  <div class="post">
    <div class="post-head"><span class="post-avatar"></span><div><b>Harwick Moss Fine Art</b><small>@HarwickMossArt</small></div></div>
    <span class="follow">Follow</span>
    Harwick Moss Fine Art Spring Sale starts today...<br>10% off everything on our website with promotional code:<br>XY537QTY... <a>hm.art/spr12</a>
    <div class="post-meta">8:28 PM - 23 Apr 2012</div>
    <div class="post-actions"><i></i><i></i><i></i></div>
  </div>
</aside>

<footer class="footer">
  <div class="footer-wash" role="img" aria-label="Grey ink splash texture"></div>
  <div class="fcol" style="left:86px">
    <h6>To Reach Us</h6>
    <div class="contact"><svg width="10" height="13" viewBox="0 0 10 13"><path d="M5 0a5 5 0 0 1 5 5c0 3-5 8-5 8S0 8 0 5a5 5 0 0 1 5-5z" fill="#fff"/><circle cx="5" cy="5" r="2" fill="#000"/></svg><span>Linden Court, 42 Marlow Row,<br>London, W2K 4PL.</span></div>
    <div class="contact"><svg width="11" height="11" viewBox="0 0 11 11"><path d="M2 0l2 3-1 1.5c.8 1.6 2 2.8 3.5 3.5L8 7l3 2-1.5 2C4 11 0 7 0 1.5z" fill="#fff"/></svg><span>+44(0)2070 114 392</span></div>
    <div class="contact"><svg width="12" height="9" viewBox="0 0 12 9"><rect width="12" height="9" fill="#fff"/><path d="M0 0l6 5 6-5" fill="none" stroke="#000"/></svg><span>info@harwickmossfineart.co.uk</span></div>
    <div class="socials"><i></i><i></i><i></i><i></i></div>
  </div>
  <div class="fcol" style="left:428px">
    <h6>Company Information</h6>
    <ul class="links"><li>&gt; Home</li><li>&gt; New Releases</li><li>&gt; About us</li><li>&gt; Artists</li><li>&gt; News</li><li>&gt; Contact us</li></ul>
  </div>
  <div class="fcol" style="left:847px">
    <h6>Newsletter Subscription</h6>
    <p>Join our mailing list for special offers and updates on new stock!!</p>
    <div class="signup"><span>Your email</span><b><svg width="20" height="18" viewBox="0 0 20 18"><path d="M0 8L20 0 16 18 10 12 8 17 7 11z" fill="#fff"/></svg></b></div>
  </div>
  <div class="copyright">Copyright © 2017 Harwick Moss Fine Art - All Rights Reserved.</div>
</footer>

</body>
</html>
```